Maplecrest Disability - Social Security Disability Attorneys

Our company is expanding to attract clients nationwide for our social security disability practice. We have a logo, but I am looking for a creative and elegant letterhead that projects an image of being technologically advanced but still professional enough for the legal field. I am looking for the "wow factor" combined with this is still professional enough for a law practice.

Requesting letterhead and business card design
Updates

Had to update and change the logo. The previous logo had a typo. Please send updates with the new logo for consideration. The letterhead and business cards should be professional enough to be used for a law firm. Thanks.

Industry/Entity Type

Law Practice, Law Firm, Healthcare Industry, Government

Colors

Designer to choose colors to be used in the design.

Requirements
Nice to have
• **Please create a vertical design for the business card**

```html
<!DOCTYPE html>
<html lang="en">
<head>
<meta charset="utf-8">
<title>Maplecrest Disability – Business Card</title>
<link rel="stylesheet" href="https://fonts.googleapis.com/css2?family=Cinzel:wght@500&family=Libre+Baskerville:wght@700&family=Nunito+Sans:wght@400&display=swap">
<style>
  :root {
    --page: #e4e4e4;
    --card-white: #f7f7f7;
    --brand-blue: #4169d8;
    --brand-orange: #f2822b;
    --ink: #3c3c3c;
    --white: #ffffff;
  }
  * { margin: 0; padding: 0; box-sizing: border-box; }
  html, body { width: 1200px; height: 1200px; overflow: hidden; }
  body { background: var(--page); position: relative; font-family: "Nunito Sans", sans-serif; }

  .card {
    position: absolute;
    left: 262px;
    width: 686px;
    height: 392px;
    border-radius: 17px;
    overflow: hidden;
  }
  .card-front { top: 165px; background: var(--card-white); }
  .card-back { top: 653px; background: var(--brand-blue); }

  .person-name {
    position: absolute; left: 43px; top: 56px;
    font-family: "Libre Baskerville", serif;
    font-size: 25px; color: var(--brand-blue); letter-spacing: 0.2px;
  }
  .person-title {
    position: absolute; left: 43px; top: 89px;
    font-size: 17px; color: var(--brand-orange);
  }
  .address {
    position: absolute; left: 43px; top: 215px;
    font-size: 15px; line-height: 19px; color: var(--ink);
  }
  .contact-list {
    position: absolute; left: 43px; top: 264px;
    list-style: none; font-size: 15px; line-height: 19.5px; color: var(--ink);
  }
  .contact-list li { display: flex; align-items: center; gap: 10px; }
  .contact-list svg { width: 14px; height: 14px; fill: var(--brand-blue); flex: none; }
  .bottom-band {
    position: absolute; left: 0; right: 0; bottom: 0; height: 10px;
    background: var(--brand-orange);
  }

  .brand-mark {
    position: absolute; left: 50%; top: 148px; transform: translateX(-50%);
    width: 34px; height: 34px; border-radius: 50%; background: var(--brand-orange);
  }
  .brand-name {
    position: absolute; left: 0; right: 0; top: 212px; text-align: center;
    font-family: "Cinzel", serif; font-size: 38px; color: var(--white);
    letter-spacing: 2.5px;
  }
  .brand-tagline {
    position: absolute; left: 0; right: 0; top: 262px; text-align: center;
    font-family: "Cinzel", serif; font-size: 11px; color: var(--white);
    letter-spacing: 3.4px;
  }
</style>
</head>
<body>
  <section class="card card-front">
    <h1 class="person-name">DANIEL WHITCOMBE</h1>
    <p class="person-title">Founder &amp; CEO</p>
    <p class="address">4120 Birchwood Court<br>Fairbanks, Alaska 99712</p>
    <ul class="contact-list">
      <li><svg viewBox="0 0 24 24" aria-hidden="true"><path d="M6.6 10.8a15.1 15.1 0 0 0 6.6 6.6l2.2-2.2c.3-.3.7-.4 1-.2 1.1.4 2.3.6 3.6.6.6 0 1 .4 1 1V20c0 .6-.4 1-1 1A17 17 0 0 1 3 4c0-.6.4-1 1-1h3.5c.6 0 1 .4 1 1 0 1.3.2 2.5.6 3.6.1.3 0 .7-.2 1z"/></svg>555-214-7730</li>
      <li><svg viewBox="0 0 24 24" aria-hidden="true"><path d="M7 1h10a2 2 0 0 1 2 2v18a2 2 0 0 1-2 2H7a2 2 0 0 1-2-2V3a2 2 0 0 1 2-2zm0 3v14h10V4zm5 15.5a1 1 0 1 0 0 2 1 1 0 0 0 0-2z"/></svg>555-389-1046</li>
      <li><svg viewBox="0 0 24 24" aria-hidden="true"><path d="M2 6h20v13H2zm2 2v.4l8 5 8-5V8l-8 5z"/></svg>info@maplecrestdisability.com</li>
      <li><svg viewBox="0 0 24 24" aria-hidden="true"><path d="M12 2a10 10 0 1 0 0 20 10 10 0 0 0 0-20zm-1 17.9A8 8 0 0 1 4.2 10L9 14.8v1a2 2 0 0 0 2 2zm6.9-2.5a2 2 0 0 0-1.9-1.4h-1v-3a1 1 0 0 0-1-1H8v-2h2a1 1 0 0 0 1-1V7h2a2 2 0 0 0 2-2v-.4a8 8 0 0 1 2.9 12.8z"/></svg>www.maplecrestdisability.com</li>
    </ul>
    <div class="bottom-band"></div>
  </section>

  <section class="card card-back">
    <div class="brand-mark" aria-hidden="true"></div>
    <h2 class="brand-name">MAPLECREST DISABILITY</h2>
    <p class="brand-tagline">SOCIAL SECURITY DISABILITY ATTORNEYS</p>
  </section>
</body>
</html>
```